Become a Mentor - For Musicians, Artists, Producers and Teachers

Here is the full creative brief:

https://files.quorvant.com/sheets/d/7kTbWmQa2_pLRz9XcN4eHs8JuYd3FoVgA6iBnCqE/view?mode=shared

Here is the background image file: https://www.stashvel.com/sh/48kdmwtnb7yrs2p/AAZm3kLPQwTx8VnHRe4jBcDu?dl=0

LOGO:
https://www.stashvel.com/sh/k382fubotn7wq6/AAJhT5LsRy2D-mKzPX9CvGhNb?dl=0

```html
<!DOCTYPE html>
<html lang="en">
<head>
<meta charset="utf-8">
<title>Become a Mentor Today – Meridian School of Music</title>
<link rel="stylesheet" href="https://fonts.googleapis.com/css2?family=Exo+2:wght@300;400;600;700;800&family=Montserrat:wght@700&display=swap">
<style>
  :root {
    --stage: #a9a9a9;
    --ink: #000000;
    --red: #e3121b;
    --sky: #1e8fe0;
    --white: #ffffff;
    --soft-white: #d9d9d9;
    --royal: #1a3fd6;
    --navy: #071a5c;
    --violet: #5b2a8c;
  }
  * { margin: 0; padding: 0; box-sizing: border-box; }
  html, body {
    width: 973px; height: 1200px; overflow: hidden;
    background: var(--stage);
  }
  .poster {
    position: absolute; left: 62px; top: 0;
    width: 849px; height: 1200px;
    background: var(--ink);
    overflow: hidden;
    font-family: "Exo 2", sans-serif;
    color: var(--white);
  }
  .studio-photo {
    position: absolute; left: 0; top: 230px; width: 849px; height: 700px;
    background:
      radial-gradient(ellipse at 30% 60%, rgba(192,50,122,.55), transparent 55%),
      radial-gradient(ellipse at 78% 45%, rgba(30,143,224,.55), transparent 55%),
      radial-gradient(ellipse at 55% 75%, rgba(120,90,60,.55), transparent 60%),
      linear-gradient(180deg, #000 0%, var(--violet) 35%, #2a1640 70%, #000 100%);
  }
  .headline-kicker {
    position: absolute; top: 36px; left: 0; width: 100%;
    text-align: center;
    font-weight: 800;
    font-size: 46px; letter-spacing: 15px; padding-left: 15px;
    color: var(--red);
  }
  .headline-lead {
    position: absolute; top: 113px; left: 0; width: 100%;
    text-align: center;
    font-weight: 300; font-size: 40px; letter-spacing: 17px; padding-left: 17px;
    color: var(--sky);
  }
  .headline-main {
    position: absolute; left: 0; width: 100%;
    display: block;
    text-align: center;
    font-family: "Montserrat", sans-serif; font-weight: 700;
    color: var(--white);
    text-shadow: 0 0 2px rgba(0,0,0,.9), 0 2px 6px rgba(0,0,0,.6);
    line-height: 1;
    white-space: nowrap;
  }
  .headline-main.mentor { top: 156px; font-size: 168px; letter-spacing: -12px; padding-left: 30px; }
  .headline-main.today { top: 292px; font-size: 218px; letter-spacing: -22px; padding-left: 10px; }
  .tagline-band {
    position: absolute; left: 0; top: 910px; width: 849px; height: 118px;
  }
  .tagline {
    position: absolute; left: 0; width: 100%; text-align: center;
    font-size: 23px; font-weight: 400; color: var(--soft-white);
  }
  .tagline strong { color: var(--red); font-weight: 700; text-transform: uppercase; }
  .tagline.first { top: 940px; }
  .tagline.second { top: 971px; }
  .apply-tag {
    position: absolute; left: 42px; top: 1060px; width: 206px; height: 33px;
    background: var(--royal);
    clip-path: polygon(0 0, 94% 0, 100% 100%, 0 100%);
    font-weight: 800; font-size: 24px; color: var(--white);
    padding-left: 14px; line-height: 33px;
  }
  .phone {
    position: absolute; left: 46px; top: 1096px;
    font-weight: 700; font-size: 49px; letter-spacing: 1px; color: var(--white);
    white-space: nowrap;
  }
  .website {
    position: absolute; left: 47px; top: 1146px;
    font-weight: 600; font-size: 24px; letter-spacing: .4px; color: var(--red);
    white-space: nowrap;
  }
  .brand {
    position: absolute; left: 606px; top: 1092px; width: 210px;
    display: flex; align-items: center; gap: 10px;
  }
  .brand-dot {
    width: 34px; height: 34px; border-radius: 50%;
    background: var(--sky); flex: none;
  }
  .brand-name {
    font-weight: 700; font-size: 19px; line-height: 1.15; color: var(--white);
    text-transform: uppercase;
  }
</style>
</head>
<body>
  <main class="poster">
    <div class="studio-photo" role="img" aria-label="Photo: two young musicians talking in a recording studio beside a mixing desk and monitor speaker, with colourful equalizer lights and music notes glowing behind them"></div>

    <h2 class="headline-kicker">START YOUR CAREER</h2>
    <p class="headline-lead">BECOME A</p>
    <h1>
      <span class="headline-main mentor">MENTOR</span>
      <span class="headline-main today">TODAY</span>
    </h1>

    <svg class="tagline-band" viewBox="0 0 849 118" aria-hidden="true">
      <defs>
        <linearGradient id="band-fade" x1="0" y1="0" x2="0" y2="1">
          <stop offset="0" stop-color="#000"/>
          <stop offset=".45" stop-color="#06103a"/>
          <stop offset="1" stop-color="#000"/>
        </linearGradient>
      </defs>
      <rect width="849" height="118" fill="url(#band-fade)"/>
      <polygon points="0,0 80,0 20,80 0,80" fill="var(--navy)"/>
      <polygon points="55,8 100,8 38,80 0,80 0,76 30,76" fill="var(--royal)"/>
      <polyline points="88,22 106,22 120,8" fill="none" stroke="var(--royal)" stroke-width="2"/>
      <polygon points="849,28 849,104 770,104 820,48" fill="var(--navy)"/>
      <polygon points="849,30 849,60 800,104 770,104" fill="var(--royal)"/>
      <polyline points="760,10 778,28 849,28" fill="none" stroke="var(--royal)" stroke-width="2"/>
      <polyline points="20,90 80,90 96,110" fill="none" stroke="var(--navy)" stroke-width="2"/>
    </svg>
    <p class="tagline first">Turn your skills and passion for <strong>Music into a Career</strong></p>
    <p class="tagline second">Designed for <strong>Musicians, Artists, Producers &amp; Teachers</strong></p>

    <div class="apply-tag">APPLY NOW</div>
    <p class="phone">CALL 1300 482 615</p>
    <p class="website">www.meridianschoolofmusic.com.au</p>

    <div class="brand">
      <span class="brand-dot"></span>
      <span class="brand-name">Meridian<br>School of Music</span>
    </div>
  </main>
</body>
</html>
```